Business card design for new eCommerce site focusing on integrity and strong businsess tactics

We need a business card that will stand out and be memorable. Something with color that matches our company logo colors. Think high end version of Pactivo. There are 2 logos provided. The parent company is called Amber Ledge Partners and we are presenting a new and very exciting eCommerce site called BrightHarborTrade.example.

Target Market(s)

Our target markets are in the Activities, Food and Beverage, Health and Beauty

Industry/Entity Type

Marketing

Contact Information for Business Card

We have 4 members that need cards...I will provide all info to the winner of the design contest
Business Address is
4870 West 63rd Avenue, Suite C207
Phoenix AZ 85731

Font styles to use
Serif
Sans Serif

Colors

Designer to choose colors to be used in the design.

Requirements
Must have
• The card must be memorable...should be unique in design but must exude integrity and be playful .
• I have provided several colors or our parent company...please feel free to use which ever
Nice to have
• I will leave this up to you. Feel free to use other images of your choosing that wraps around our client.....Activities, Dining, Health, Beauty
Should not have
• just dont be boring

```html
<!DOCTYPE html>
<html lang="en">
<head>
<meta charset="utf-8">
<title>BrightHarborTrade.example business card</title>
<link rel="stylesheet" href="https://fonts.googleapis.com/css2?family=Questrial&display=swap">
<style>
  :root{
    --bg:#3a3b3d;
    --paper:#ffffff;
    --blue:#2f7fb3;
    --blue-light:#4a9ac4;
    --green:#6fb33a;
    --green-light:#8cc84b;
    --ink:#4a4a4a;
  }
  *{margin:0;padding:0;box-sizing:border-box}
  html,body{width:1200px;height:834px;overflow:hidden;background:var(--bg)}
  body{position:relative;font-family:"Questrial",sans-serif}
  .card{position:absolute;width:600px;height:343px;background:var(--paper);overflow:hidden;box-shadow:0 10px 30px rgba(0,0,0,.35)}
  .card svg.art{position:absolute;inset:0;width:100%;height:100%}
  .card--front{left:70px;top:50px}
  .card--back{left:530px;top:440px}

  .brand{position:absolute}
  .brand__name{font-size:24px;color:var(--green);line-height:1;white-space:nowrap;display:flex;align-items:center;gap:9px}
  .brand__dot{width:20px;height:20px;border-radius:50%;background:var(--blue);flex:none}
  .brand__tagline{font-size:12px;color:var(--ink);letter-spacing:.5px;margin:6px 0 0 29px;white-space:nowrap}
  .card--front .brand{left:56px;top:112px}
  .card--back .brand{left:300px;top:118px}
  .card--back .brand__name{font-size:18px;gap:8px}
  .card--back .brand__dot{width:15px;height:15px}
  .card--back .brand__tagline{font-size:9.5px;margin-left:23px}

  .parent{position:absolute;right:44px;top:26px;display:flex;flex-direction:column;align-items:center;gap:8px}
  .parent__mark{width:52px;height:52px;border-radius:50%;background:var(--green-light)}
  .parent__name{font-size:12px;color:var(--green);white-space:nowrap}

  .contact{position:absolute;left:34px;top:78px;color:#fff}
  .contact__name{font-size:20px;letter-spacing:1px;font-weight:400}
  .contact__role{font-size:14px;color:var(--green-light);margin-top:2px}
  .contact__address{font-size:11.5px;line-height:1.7;margin-top:18px}
  .contact__list{list-style:none;margin-top:14px;font-size:11.5px;line-height:1}
  .contact__list li{display:flex;align-items:center;gap:10px;margin-bottom:8px}
  .contact__list svg{width:13px;height:13px;flex:none}
</style>
</head>
<body>

<section class="card card--front">
  <svg class="art" viewBox="0 0 600 343" preserveAspectRatio="none" aria-hidden="true">
    <path d="M0,282 C200,292 330,262 420,192 C480,145 530,128 600,122 L600,343 L0,343 Z" fill="var(--green)"/>
    <path d="M0,294 C200,304 330,274 420,204 C480,157 530,140 600,134 L600,343 L0,343 Z" fill="var(--blue)" stroke="#fff" stroke-width="3"/>
  </svg>
  <div class="brand">
    <div class="brand__name"><span class="brand__dot"></span>BrightHarborTrade.example</div>
    <div class="brand__tagline">Activities-Dining-Health-Beauty</div>
  </div>
  <div class="parent">
    <span class="parent__mark"></span>
    <span class="parent__name">Amber Ledge Partners</span>
  </div>
</section>

<section class="card card--back">
  <svg class="art" viewBox="0 0 600 343" preserveAspectRatio="none" aria-hidden="true">
    <defs>
      <linearGradient id="panelBlue" x1="0" y1="0" x2="1" y2="1">
        <stop offset="0" stop-color="var(--blue-light)"/>
        <stop offset="1" stop-color="var(--blue)"/>
      </linearGradient>
      <linearGradient id="fieldGreen" x1="0" y1="0" x2="1" y2="1">
        <stop offset="0" stop-color="var(--green-light)"/>
        <stop offset="1" stop-color="var(--green)"/>
      </linearGradient>
    </defs>
    <path d="M250,0 L600,0 L600,60 C520,100 410,112 310,100 C275,92 258,50 250,0 Z" fill="url(#fieldGreen)"/>
    <path d="M600,170 C460,180 360,250 330,343 L600,343 Z" fill="url(#fieldGreen)" stroke="var(--blue)" stroke-width="4"/>
    <path d="M0,0 L250,0 C300,100 320,230 270,343 L0,343 Z" fill="url(#panelBlue)"/>
  </svg>
  <div class="contact">
    <h1 class="contact__name">DANA WHITFIELD</h1>
    <p class="contact__role">President</p>
    <p class="contact__address">4870 West 63rd Avenue, Suite C207<br>Phoenix AZ 85731</p>
    <ul class="contact__list">
      <li><svg viewBox="0 0 16 16" fill="none" stroke="var(--green-light)" stroke-width="1.6"><path d="M4 2 L6 5 L5 7 Q7 10 9 11 L11 10 L14 12 L12 14 Q5 13 2 4 Z"/></svg>555-014-2870</li>
      <li><svg viewBox="0 0 16 16" fill="none" stroke="var(--green-light)" stroke-width="1.6"><rect x="1.5" y="3.5" width="13" height="9"/><path d="M1.5 3.5 L8 9 L14.5 3.5"/></svg>dana@brightharbortrade.example</li>
      <li><svg viewBox="0 0 16 16" fill="none" stroke="var(--green-light)" stroke-width="1.4"><circle cx="8" cy="8" r="6.3"/><ellipse cx="8" cy="8" rx="2.8" ry="6.3"/><path d="M1.7 8 H14.3"/></svg>www.brightharbortrade.example</li>
    </ul>
  </div>
  <div class="brand">
    <div class="brand__name"><span class="brand__dot"></span>BrightHarborTrade.example</div>
    <div class="brand__tagline">Activities-Dining-Health-Beauty</div>
  </div>
</section>

</body>
</html>
```